New business card/stationary for a consulting company

I am looking for a clean and very professional looking business card for my consulting company as well as corresponding stationary. I am uploading our logo. I like simple and powerful for the feel. No graphics but I am open on everything else. Below is my contact information but would like the final to be in a version I can add my employees information into and print. Thank you.

Daniel Whitcombe
dan@ferncliffadvisory.com
2870 North 9th Avenue, Summit Floor, Elm Ridge, Illinois 60531
www.ferncliffadvisory.com

Industry/Entity Type

Consulting

Contact Information for Business Card

Daniel Whitcombe
dan@ferncliffadvisory.com
www.ferncliffadvisory.com

Font styles to use
Serif
Sans Serif

Requirements
Must have
• Our logo and the business card details.
Nice to have
• our website www.ferncliffadvisory.com

```html
<!DOCTYPE html>
<html lang="en">
<head>
<meta charset="utf-8">
<title>Ferncliff Advisory – Business Card</title>
<link rel="stylesheet" href="https://fonts.googleapis.com/css2?family=Marcellus&family=Roboto:wght@400&display=swap">
<style>
  :root {
    --navy: #142c5c;
    --navy-deep: #0f2553;
    --paper: #f4f4f4;
    --paper-shade: #e9e9e9;
    --backdrop: #e4e4e4;
    --rule: #c9c9c9;
    --ink: #222a35;
    --white: #ffffff;
  }
  * { box-sizing: border-box; margin: 0; padding: 0; }
  html, body {
    width: 1200px; height: 576px; overflow: hidden;
    background: var(--backdrop);
  }
  .canvas { position: relative; width: 1200px; height: 576px; }
  .card {
    position: absolute;
    width: 484px; height: 292px;
    border-radius: 13px;
    box-shadow: 0 3px 6px rgba(0,0,0,0.18);
    text-align: center;
  }
  .card--front { left: 82px; top: 139px; background: var(--navy); color: var(--white); }
  .card--back {
    left: 602px; top: 138px;
    background: linear-gradient(180deg, var(--paper) 0%, var(--paper-shade) 100%);
    color: var(--navy);
  }
  .brand-square {
    position: absolute; left: 50%; transform: translateX(-50%);
  }
  .card--front .brand-square { top: 98px; width: 40px; height: 40px; background: var(--white); }
  .card--back .brand-square { top: 44px; width: 44px; height: 44px; background: var(--navy); }
  .brand-name {
    position: absolute; left: 0; right: 0;
    font-family: "Marcellus", serif;
    letter-spacing: 1px;
    line-height: 1;
  }
  .card--front .brand-name { top: 168px; font-size: 25px; }
  .card--back .brand-name { top: 113px; font-size: 29px; }
  .person-name {
    position: absolute; left: 0; right: 0; top: 188px;
    font-family: "Marcellus", serif; font-size: 18px; letter-spacing: 1px; line-height: 1;
  }
  .divider {
    position: absolute; left: 27px; right: 32px; top: 216px;
    border-top: 1px solid var(--rule);
  }
  .contact {
    position: absolute; left: 53px; top: 230px;
    font-family: "Roboto", sans-serif; font-size: 12.5px; color: var(--ink);
    text-align: left; line-height: 19px;
  }
  .contact-row { display: flex; align-items: center; white-space: nowrap; }
  .contact-item { display: inline-flex; align-items: center; margin-right: 10px; }
  .contact-item svg { margin-right: 6px; fill: var(--navy-deep); }
</style>
</head>
<body>
<main class="canvas">
  <section class="card card--front">
    <div class="brand-square"></div>
    <div class="brand-name">FERNCLIFF ADVISORY</div>
  </section>

  <section class="card card--back">
    <div class="brand-square"></div>
    <div class="brand-name">FERNCLIFF ADVISORY</div>
    <div class="person-name">DANIEL WHITCOMBE</div>
    <div class="divider"></div>
    <div class="contact">
      <div class="contact-row">
        <span class="contact-item">
          <svg width="11" height="8" viewBox="0 0 11 8" aria-hidden="true"><path d="M0 0h11v8H0z M0.8 0.8 5.5 4.6 10.2 0.8z" fill-rule="evenodd"/></svg>
          dan@ferncliffadvisory.com
        </span>
        <span class="contact-item">
          <svg width="11" height="11" viewBox="0 0 12 12" aria-hidden="true"><circle cx="6" cy="6" r="5.5"/><path d="M0.5 6h11M6 0.5c-2.5 3-2.5 8 0 11M6 0.5c2.5 3 2.5 8 0 11" stroke="#f0f0f0" stroke-width="0.9" fill="none"/></svg>
          www.ferncliffadvisory.com
        </span>
      </div>
      <div class="contact-row">
        <span class="contact-item">
          <svg width="10" height="13" viewBox="0 0 10 13" aria-hidden="true"><path d="M5 0a5 5 0 0 1 5 5c0 3.5-5 8-5 8S0 8.5 0 5a5 5 0 0 1 5-5zm0 3a2 2 0 1 0 0 4 2 2 0 0 0 0-4z" fill-rule="evenodd"/></svg>
          2870 North 9th Avenue, Summit Floor, Elm Ridge, Illinois 60531
        </span>
      </div>
    </div>
  </section>
</main>
</body>
</html>
```